Single-sided business card for restaurant velmora with new logo made on this site

Business card options with new logo including restaurant name, address, phone number and website. This business card is single-sided only and will be presented at the hostess desk for clients to take. I would like to see options based on a cream card background, a white card background, a yellow card background and a burgundy colored background. It needs to be elegant and traditional.

Target Market(s)

local and international crowd

Industry/Entity Type

restaurant

Contact Information for Business Card

address, website and phone number

Font styles to use
Serif

Colors
EE7325
F08F49
F5BC92
FAE3D3
FDF4ED

Requirements
Must have
• new logo, address, phone number, website
Should not have
• more than three colors

```html
<!DOCTYPE html>
<html lang="es">
<head>
<meta charset="utf-8">
<title>Velmora – Tarjeta de presentación</title>
<link href="https://fonts.googleapis.com/css2?family=Crimson+Pro:wght@400;700&display=swap" rel="stylesheet">
<style>
  :root {
    --backdrop: #e4e4e4;
    --cream: #fdedd2;
    --burgundy: #371719;
    --burgundy-light: #4a2428;
    --gold: #f4b431;
    --ink: #3b1a1d;
  }
  * { margin: 0; padding: 0; box-sizing: border-box; }
  html, body {
    width: 1200px;
    height: 940px;
    overflow: hidden;
    background: var(--backdrop);
    font-family: "Crimson Pro", Georgia, serif;
  }
  .business-card {
    position: absolute;
    left: 100px;
    top: 185px;
    width: 1000px;
    height: 570px;
    border-radius: 30px;
    overflow: hidden;
    background: var(--cream);
  }
  .card-shapes { position: absolute; inset: 0; }
  .brand {
    position: absolute;
    left: 40px;
    top: 66px;
    width: 304px;
    text-align: center;
  }
  .brand-square {
    display: block;
    width: 148px;
    height: 148px;
    margin: 0 auto 34px;
    background: var(--gold);
  }
  .brand-name {
    color: var(--ink);
    font-size: 46px;
    font-weight: 400;
    letter-spacing: 10px;
    line-height: 1;
    padding-left: 10px;
  }
  .contact {
    position: absolute;
    right: 42px;
    top: 346px;
    text-align: right;
    color: var(--gold);
  }
  .contact-name { font-size: 26px; font-weight: 700; line-height: 32px; }
  .contact-address { font-size: 25px; font-weight: 400; line-height: 32px; }
  .reservations-label {
    font-size: 36px;
    font-weight: 700;
    line-height: 40px;
    margin-top: 8px;
  }
  .reservations-phone {
    display: flex;
    align-items: center;
    justify-content: flex-end;
    gap: 8px;
    font-size: 48px;
    font-weight: 400;
    line-height: 50px;
  }
  .phone-icon { width: 34px; height: 34px; }
  .website {
    position: absolute;
    left: 60px;
    top: 500px;
    color: var(--gold);
    font-size: 26px;
    font-weight: 700;
    letter-spacing: 0.5px;
  }
</style>
</head>
<body>
  <div class="business-card">
    <svg class="card-shapes" viewBox="0 0 1000 570" width="1000" height="570" aria-hidden="true">
      <defs>
        <linearGradient id="burgundy-fill" x1="1" y1="0" x2="0" y2="1">
          <stop offset="0" stop-color="var(--burgundy-light)"/>
          <stop offset="0.6" stop-color="var(--burgundy)"/>
        </linearGradient>
      </defs>
      <path class="gold-swoosh" fill="var(--gold)"
            d="M0 381 C 260 440, 520 405, 731 248 C 530 412, 270 460, 0 410 Z"/>
      <path class="burgundy-field" fill="url(#burgundy-fill)"
            d="M0 418 C 300 478, 640 420, 1000 38 L1000 570 L0 570 Z"/>
    </svg>

    <div class="brand">
      <span class="brand-square"></span>
      <div class="brand-name">VELMORA</div>
    </div>

    <div class="contact">
      <div class="contact-name">Restaurant Velmora</div>
      <div class="contact-address">Jacaranda 418, Bahías de Huatulco</div>
      <div class="contact-address">Oaxaca CP 70950</div>
      <div class="reservations-label">Reservaciones</div>
      <div class="reservations-phone">
        <svg class="phone-icon" viewBox="0 0 24 24" fill="none" stroke="currentColor" stroke-width="1.4" stroke-linejoin="round" aria-hidden="true">
          <path d="M5 3 L8.5 3 L10 7.5 L8 9 C9 11.5 12.5 15 15 16 L16.5 14 L21 15.5 L21 19 C21 20 20 21 19 21 C10.5 20.5 3.5 13.5 3 5 C3 4 4 3 5 3 Z"/>
          <path d="M14 3.5 A6.5 6.5 0 0 1 20.5 10"/>
          <path d="M14 6.5 A3.5 3.5 0 0 1 17.5 10"/>
        </svg>
        <span>958-555-0142</span>
      </div>
    </div>

    <div class="website">www.Velmora.com.mx</div>
  </div>
</body>
</html>
```